Italian restaurant needs new site

Need to make our website better.

Must have reservation module

Must be able to sell wine tasting tours and wine pairing tours and intégrate with dunmo desk

Blog

Social media

Wandervane ranking and last review.
Updates

Number of Pages Required

1 page

Font styles to use
Serif

Requirements
Must have
• Reservation module
• Marketplace to buy wine pairings and gift certificates
• Wandervane review
• Kindlepost posts
• All info from old site

```html
<!DOCTYPE html>
<html lang="en">
<head>
<meta charset="utf-8">
<title>Vinora Bistro – Italian Restaurant in Cabo San Lucas</title>
<link rel="stylesheet" href="https://fonts.googleapis.com/css2?family=Lora:wght@400;700&family=Open+Sans:wght@400;600&display=swap">
<style>
:root{
  --wine:#8b1c26;
  --wine-dark:#6e1219;
  --ink:#333333;
  --muted:#8a8a8a;
  --line:#dddddd;
  --paper:#ffffff;
  --mist:#eeeeee;
  --serif:'Lora', Georgia, serif;
  --sans:'Open Sans', Arial, sans-serif;
}
*{box-sizing:border-box;margin:0;padding:0}
html,body{width:1200px;height:3435px;overflow:hidden;background:var(--paper);color:var(--ink);font-family:var(--sans)}
.page{position:relative;width:1200px;height:3435px}
.wrap{position:absolute;left:133px;width:934px}

/* header */
.site-header{position:absolute;top:0;left:0;width:1200px;height:120px;background:rgba(255,255,255,.96);z-index:2}
.brand{position:absolute;left:132px;top:14px;display:flex;align-items:center;gap:10px}
.brand-mark{width:34px;height:34px;border-radius:50%;background:var(--wine)}
.brand-name{font-family:var(--serif);color:var(--wine);font-size:30px;line-height:1;font-weight:400}
.brand-tag{font-family:var(--serif);color:var(--wine);font-size:9px;letter-spacing:1px;margin-top:6px}
.btn-reserve{position:absolute;left:923px;top:24px;width:145px;height:38px;background:var(--wine);color:#fff;font-family:var(--serif);font-size:13px;display:flex;align-items:center;justify-content:center;gap:7px;border-radius:3px}
.main-nav{position:absolute;right:133px;top:80px;display:flex;gap:34px;font-family:var(--serif);font-size:13px}
.main-nav a{color:#222;text-decoration:none}
.main-nav a.is-active{color:var(--wine)}

/* hero */
.hero{position:absolute;top:120px;left:0;width:1200px;height:494px;background:linear-gradient(90deg,#4a2e1e 0%,#6b4630 40%,#7a4d2e 60%,#b4542a 80%,#5a3520 100%)}
.hero-title{position:absolute;left:136px;top:150px;width:380px;font-family:var(--serif);font-weight:700;font-size:40px;line-height:52px;color:#fff;text-transform:uppercase}
.slide-arrow{position:absolute;top:232px;width:26px;height:26px;border-radius:50%;background:rgba(0,0,0,.55);display:flex;align-items:center;justify-content:center}

/* headings */
.section-title{font-family:var(--serif);color:var(--wine);font-size:36px;font-weight:400;text-align:center;text-transform:uppercase;letter-spacing:.5px}

/* mission */
.mission{top:680px}
.mission p{font-size:13px;line-height:21px;text-align:center;margin-top:18px;color:#333}
.mission p + p{margin-top:20px}

/* reserve */
.reserve{position:absolute;top:928px;left:0;width:1200px;height:302px;background:linear-gradient(180deg,#8e2a32,#7d1e27)}
.reserve .section-title{color:#fff;margin-top:40px;font-size:34px}
.form-row{position:absolute;left:133px;width:934px;display:flex;gap:20px}
.field{flex:1;height:42px;border:1px solid rgba(255,255,255,.7);color:#fff;font-size:12px;padding:0 12px;display:flex;align-items:center;justify-content:space-between}
.btn-submit{position:absolute;left:552px;top:217px;width:96px;height:39px;background:#1c1c1c;color:#fff;font-family:var(--serif);font-size:14px;display:flex;align-items:center;justify-content:center}

/* tours */
.tour{position:absolute;top:1285px;width:440px;height:281px}
.tour-title{position:absolute;left:16px;top:95px;font-family:var(--serif);font-weight:700;font-size:22px;line-height:26px;color:#fff;text-transform:uppercase}
.tour-btn{position:absolute;left:16px;top:153px;border:1px solid #fff;color:#fff;font-size:11px;padding:6px 12px}

/* blog */
.blog-card{position:absolute;top:1667px;width:298px;height:440px;border:1px solid var(--line)}
.blog-img{height:200px}
.blog-body{padding:22px 22px}
.blog-body h3{font-size:17px;line-height:23px;font-weight:400;color:#777}
.blog-date{font-size:12px;margin-top:10px;color:#333}
.blog-excerpt{font-size:11px;line-height:17px;color:#aaa;margin-top:18px}
.btn-more{display:inline-block;margin-top:20px;background:#eeeeee;color:#777;font-size:11px;padding:9px 16px}
.view-more{position:absolute;top:2127px;left:0;width:1200px;text-align:center;font-family:var(--serif);font-size:15px;text-decoration:underline;color:#333}

/* testimonials */
.testimonials{position:absolute;top:2226px;left:0;width:1200px;height:300px;background:var(--mist)}
.testimonials .section-title{margin-top:38px;font-size:34px}
.quote{width:1060px;margin:14px auto 0;text-align:center;font-size:20px;line-height:30px;color:#333}
.cite{text-align:center;font-size:13px;margin-top:8px}
.rating-brand{display:flex;justify-content:center;align-items:center;gap:6px;margin-top:10px;font-size:15px;font-weight:600;color:#333}
.rating-dot{width:14px;height:14px;border-radius:50%;background:#589442}
.rank{text-align:center;font-size:11px;margin-top:6px}
.rating-badge{width:70px;height:13px;margin:6px auto 0;border-radius:7px;background:#589442}

/* menu teaser */
.menu-teaser{top:2596px}
.menu-teaser p{font-size:13px;line-height:20px;text-align:center;margin-top:14px}
.btn-menu{position:absolute;left:387px;top:124px;width:160px;height:46px;background:var(--wine);color:#fff;font-family:var(--serif);font-size:13px;display:flex;align-items:center;justify-content:center}
.divider{position:absolute;top:2846px;left:133px;width:934px;height:1px;background:var(--line)}

/* contact */
.contact{top:2914px}
.map{position:absolute;top:2991px;left:133px;width:467px;height:318px;background:linear-gradient(135deg,#e9e6df 0%,#dfe4e0 45%,#b9d3e6 75%,#a9c8e0 100%)}
.contact-panel{position:absolute;top:2991px;left:600px;width:467px;height:318px;background:var(--wine);color:#fff;padding:56px 34px}
.contact-line{display:flex;align-items:center;gap:14px;font-family:var(--serif);font-size:15px;height:30px}
.socials{display:flex;gap:14px;margin-top:28px}
.social{height:46px;padding:0 10px;border:1px solid #fff;display:flex;align-items:center;font-family:var(--serif);font-size:12px}

/* footer */
.footer-nav{position:absolute;top:3343px;left:0;width:1200px;text-align:center;font-size:11px;color:#666}
.footer-nav span{margin:0 9px}
.copyright{position:absolute;top:3372px;left:0;width:1200px;text-align:center;font-size:10px;color:#888}
</style>
</head>
<body>
<div class="page">

  <header class="site-header">
    <div class="brand">
      <div class="brand-mark"></div>
      <div>
        <div class="brand-name">Vinora Bistro</div>
        <div class="brand-tag">ITALIAN CUISINE &amp; WINE BAR</div>
      </div>
    </div>
    <div class="btn-reserve">
      <svg width="12" height="12" viewBox="0 0 12 12"><rect x="1" y="2" width="9" height="9" fill="none" stroke="#fff" stroke-width="1.3"/><path d="M5 7 L11 1" stroke="#fff" stroke-width="1.3"/></svg>
      RESERVATIONS
    </div>
    <nav class="main-nav">
      <a class="is-active" href="#">HOME</a><a href="#">MENU</a><a href="#">BLOG</a><a href="#">REVIEW</a><a href="#">CONTACT US</a>
    </nav>
  </header>

  <section class="hero" role="img" aria-label="Plate of shrimp pasta with tomatoes and parsley on a rustic wooden table">
    <h1 class="hero-title">Vinora Bistro Italian Restaurant in Cabo San Lucas</h1>
    <div class="slide-arrow" style="left:24px"><svg width="10" height="10" viewBox="0 0 10 10"><path d="M7 1 L3 5 L7 9" fill="none" stroke="#fff" stroke-width="2"/></svg></div>
    <div class="slide-arrow" style="right:24px"><svg width="10" height="10" viewBox="0 0 10 10"><path d="M3 1 L7 5 L3 9" fill="none" stroke="#fff" stroke-width="2"/></svg></div>
  </section>

  <section class="wrap mission">
    <h2 class="section-title">Our Mission</h2>
    <p>To gather those who have impacted our lives and supported us in this wonderful town, bring them high quality food and wines, while simultaneously offering affordable prices to locals and visitors. We invite you to come and enjoy a glass of wine and to delight in our exquisite range of unique menu options. Created by hands with years of experience in traditional Mediterranean cuisine, our refreshing, family-style salads and tapas, Italian antipastos, fresh seafood dishes, and baked lasagna will transport your senses.</p>
    <p>It will undoubtedly be an unforgettable experience for your pallet!</p>
  </section>

  <section class="reserve">
    <h2 class="section-title">Reserve Now</h2>
    <div class="form-row" style="top:95px">
      <div class="field">Name</div><div class="field">Email</div><div class="field">Phone</div>
      <div class="field">Date <svg width="12" height="12" viewBox="0 0 12 12"><rect x="1" y="2" width="10" height="9" fill="none" stroke="#fff"/><path d="M1 5 H11 M4 1 V3 M8 1 V3" stroke="#fff"/></svg></div>
    </div>
    <div class="form-row" style="top:160px"><div class="field">Message</div></div>
    <div class="btn-submit">SUBMIT</div>
  </section>

  <article class="tour" style="left:133px;background:linear-gradient(160deg,#c9a779 0%,#6d5a3e 45%,#3b2a1c 100%)" role="img" aria-label="Wine bottle and glasses with cheese platter at sunset">
    <div class="tour-title">Wine Tasting<br>Tours</div>
    <div class="tour-btn">BOOK NOW</div>
  </article>
  <article class="tour" style="left:627px;background:linear-gradient(160deg,#6a5a55 0%,#3a2d2a 50%,#7a2a2e 100%)" role="img" aria-label="Hand holding a glass of red wine at a gathering">
    <div class="tour-title">Wine Pairing<br>Tours</div>
    <div class="tour-btn">BOOK NOW</div>
  </article>

  <h2 class="section-title" style="position:absolute;top:1610px;left:0;width:1200px">Blog</h2>

  <article class="blog-card" style="left:133px">
    <div class="blog-img" role="img" aria-label="Plated gourmet dish on a white plate" style="background:linear-gradient(135deg,#f4f4f2,#d9d6d0 60%,#9a8c6e)"></div>
    <div class="blog-body">
      <h3>Praesent iaculis faucibus urna sit amet lacinia.</h3>
      <div class="blog-date">24 July, 2017</div>
      <p class="blog-excerpt">Fusce nec leo ac urna pulvinar auctor. Mauris bibendum fringilla velit. Nulla in lorem at massa pellentesque posuere.</p>
      <span class="btn-more">Read more</span>
    </div>
  </article>
  <article class="blog-card" style="left:451px">
    <div class="blog-img" role="img" aria-label="Red wine bottle lying among corks" style="background:linear-gradient(135deg,#2a1a12,#6a1a1c 55%,#a67c52)"></div>
    <div class="blog-body">
      <h3>Praesent iaculis faucibus urna sit amet lacinia.</h3>
      <div class="blog-date">24 July, 2017</div>
      <p class="blog-excerpt">Fusce nec leo ac urna pulvinar auctor. Mauris bibendum fringilla velit. Nulla in lorem at massa pellentesque posuere.</p>
      <span class="btn-more">Read more</span>
    </div>
  </article>
  <article class="blog-card" style="left:769px">
    <div class="blog-img" role="img" aria-label="Row of wine bottles in a dim cellar" style="background:linear-gradient(135deg,#1a120c,#5a3a1c 55%,#c28a3a)"></div>
    <div class="blog-body">
      <h3>Praesent iaculis faucibus urna sit amet lacinia.</h3>
      <div class="blog-date">24 July, 2017</div>
      <p class="blog-excerpt">Fusce nec leo ac urna pulvinar auctor. Mauris bibendum fringilla velit. Nulla in lorem at massa pellentesque posuere.</p>
      <span class="btn-more">Read more</span>
    </div>
  </article>
  <div class="view-more">And View More</div>

  <section class="testimonials">
    <h2 class="section-title">Testimonials</h2>
    <p class="quote">" Phasellus nisl est, condimentum vitae faucibus in, sollicitudin vel metus. Nunc sit amet consequat risus. Curabitur ac elit leo. In eleifend dui tellus, in scelerisque elit porttitor et. "</p>
    <p class="cite">- Dana Rell, City</p>
    <div class="rating-brand"><span class="rating-dot"></span>Wandervane</div>
    <p class="rank">#9 of 572 places to eat in Cabo San Lucas</p>
    <div class="rating-badge"></div>
    <svg style="position:absolute;left:22px;top:132px" width="16" height="26" viewBox="0 0 16 26"><path d="M13 2 L3 13 L13 24" fill="none" stroke="#999" stroke-width="2.5"/></svg>
    <svg style="position:absolute;right:22px;top:132px" width="16" height="26" viewBox="0 0 16 26"><path d="M3 2 L13 13 L3 24" fill="none" stroke="#999" stroke-width="2.5"/></svg>
  </section>

  <section class="wrap menu-teaser">
    <h2 class="section-title">Vestibulum Condimentum Risus Posuere</h2>
    <p>Aliquam erat volutpat. Quisque aliquet ex nec est vestibulum pulvinar. Pellentesque convallis molestie enim sit amet efficitur. Etiam id imperdiet lectus. Vivamus lacus justo, ultrices nec erat in, euismod iaculis mauris. Vivamus eleifend vitae nulla vel malesuada. In ac malesuada lacus, et consectetur ante. Fusce vitae lectus sit amet mi pulvinar maximus. Aenean placerat, nibh vel accumsan aliquet.</p>
    <div class="btn-menu">VIEW OUR MENU</div>
  </section>
  <div class="divider"></div>

  <section class="wrap contact">
    <h2 class="section-title">Contact Us</h2>
  </section>
  <div class="map" role="img" aria-label="Street map of central Cabo San Lucas showing the restaurant location near the marina"></div>
  <div class="contact-panel">
    <div class="contact-line"><svg width="12" height="16" viewBox="0 0 12 16"><path d="M6 15 C2 9 1 7 1 5.5 A5 5 0 0 1 11 5.5 C11 7 10 9 6 15Z" fill="#fff"/><circle cx="6" cy="5.5" r="2" fill="#8b1c26"/></svg>Calle Olivo 12, Centro, Cabo San Lucas, Mexico</div>
    <div class="contact-line"><svg width="12" height="14" viewBox="0 0 12 14"><rect x="2" y="0.5" width="8" height="13" rx="1.5" fill="#fff"/><rect x="3.5" y="2" width="5" height="8" fill="#8b1c26"/></svg>555 0142</div>
    <div class="contact-line"><svg width="14" height="10" viewBox="0 0 14 10"><rect width="14" height="10" fill="#fff"/><path d="M0 0 L7 6 L14 0" fill="none" stroke="#8b1c26"/></svg>hello@vinorabistro.example</div>
    <div class="contact-line"><svg width="14" height="10" viewBox="0 0 14 10"><rect width="14" height="10" fill="#fff"/><path d="M0 0 L7 6 L14 0" fill="none" stroke="#8b1c26"/></svg>open daily from 5 to 12 am</div>
    <div class="socials"><span class="social">Kindlepost</span><span class="social">Snapframe</span><span class="social">Chirpline</span></div>
  </div>

  <div class="footer-nav"><span>Home</span>|<span>Menu</span>|<span>Blog</span>|<span>Review</span>|<span>Contact Us</span></div>
  <div class="copyright">Copyright © 2017 Vinora Bistro - All rights reserved.</div>

</div>
</body>
</html>
```